Our companies name is The Gilded Ladle and we specialize in craft cupcakes, what I mean by that is that we bake our cupcakes with craft beer and other alcoholic drinks. We are trying to focus on being elegant but at the same time unpretentious. Since we are incorporating beer in our cupcakes we want the business card to have our logo in the front and our information in the back.

Once we select the best design we will provide the contact information to be added. Thank you.

Industry/Entity Type

Business

Font styles to use
Decorative
Script

Requirements
Must have
• Round corners
Should not have
• Square corners

```html
<!DOCTYPE html>
<html lang="en">
<head>
<meta charset="utf-8">
<title>The Gilded Ladle – Business Card</title>
<link rel="stylesheet" href="https://fonts.googleapis.com/css2?family=Exo+2:wght@400;500;600&family=Michroma&display=swap">
<style>
  :root {
    --page-bg: #e9e7e4;
    --card-white: #ffffff;
    --card-grey: #e2e2e2;
    --ink: #1c1c1c;
    --ink-soft: #3a3a3a;
    --band-black: #0d0d0d;
    --accent-orange: #f05a22;
    --brand-dark: #253b3f;
  }
  * { box-sizing: border-box; margin: 0; padding: 0; }
  html, body {
    width: 1200px; height: 900px; overflow: hidden;
    background: var(--page-bg);
    font-family: "Exo 2", sans-serif;
  }
  .card {
    position: absolute;
    left: 100px; top: 160px;
    width: 1000px; height: 580px;
    border-radius: 60px;
    overflow: hidden;
    background: radial-gradient(ellipse at 55% 40%, var(--card-white) 0%, var(--card-grey) 100%);
    box-shadow: 0 20px 40px rgba(0,0,0,0.18);
  }
  .card__waves { position: absolute; inset: 0; width: 100%; height: 100%; }
  .holder {
    position: absolute; right: 64px; top: 58px; text-align: right;
  }
  .holder__name {
    font-family: "Michroma", sans-serif;
    font-size: 24px; letter-spacing: 1px; color: var(--ink);
  }
  .holder__role {
    font-family: "Michroma", sans-serif;
    font-size: 13px; letter-spacing: 2px; color: var(--ink-soft);
    margin-top: 4px;
  }
  .contact {
    position: absolute; right: 64px; top: 150px;
    list-style: none; text-align: right;
  }
  .contact__item {
    display: flex; justify-content: flex-end; align-items: center; gap: 10px;
    font-size: 16px; letter-spacing: 1px; color: var(--ink);
    height: 28px;
  }
  .contact__icon { width: 18px; height: 18px; fill: none; stroke: var(--ink); stroke-width: 2; }
  .brand {
    position: absolute; left: 60px; top: 170px;
    display: flex; align-items: center; gap: 16px;
  }
  .brand__dot {
    width: 120px; height: 120px; border-radius: 50%; background: var(--brand-dark);
  }
  .brand__name {
    font-family: "Exo 2", sans-serif; font-weight: 600;
    font-size: 30px; color: var(--brand-dark);
  }
  .address {
    position: absolute; left: 60px; top: 362px;
    font-size: 20px; font-style: normal; letter-spacing: 1px; line-height: 1.4; color: var(--ink);
  }
</style>
</head>
<body>
  <div class="card">
    <svg class="card__waves" viewBox="0 0 1000 580" preserveAspectRatio="none" aria-hidden="true">
      <path class="wave-orange" fill="var(--accent-orange)" d="M250,478 C560,455 860,360 1000,220 L1000,278 C860,400 600,468 250,478 Z"/>
      <path class="wave-black" fill="var(--band-black)" d="M0,462 C360,500 800,440 1000,300 L1000,580 L0,580 Z"/>
    </svg>

    <div class="holder">
      <div class="holder__name">DANA KERROW</div>
      <div class="holder__role">PRESIDENT</div>
    </div>

    <ul class="contact">
      <li class="contact__item">010 555 0142
        <svg class="contact__icon" viewBox="0 0 24 24"><path d="M5 3h4l2 5-3 2a11 11 0 0 0 6 6l2-3 5 2v4a2 2 0 0 1-2 2A18 18 0 0 1 3 5a2 2 0 0 1 2-2z"/></svg>
      </li>
      <li class="contact__item">010 555 0143
        <svg class="contact__icon" viewBox="0 0 24 24"><rect x="7" y="2" width="10" height="20" rx="2"/><line x1="11" y1="18" x2="13" y2="18"/></svg>
      </li>
      <li class="contact__item">010 555 0144
        <svg class="contact__icon" viewBox="0 0 24 24"><rect x="4" y="9" width="16" height="12" rx="1"/><rect x="8" y="3" width="8" height="6"/><line x1="8" y1="14" x2="16" y2="14"/></svg>
      </li>
      <li class="contact__item">dana@gildedladle.com
        <svg class="contact__icon" viewBox="0 0 24 24"><rect x="3" y="5" width="18" height="14" rx="1"/><path d="M3 6l9 7 9-7"/></svg>
      </li>
      <li class="contact__item">www.gildedladle.com
        <svg class="contact__icon" viewBox="0 0 24 24"><circle cx="12" cy="12" r="9"/><ellipse cx="12" cy="12" rx="4" ry="9"/><line x1="3" y1="12" x2="21" y2="12"/></svg>
      </li>
    </ul>

    <div class="brand">
      <span class="brand__dot"></span>
      <span class="brand__name">The Gilded Ladle</span>
    </div>

    <address class="address">
      27 Baker Lane, Suite 4<br>Millbrook Road KTV
    </address>
  </div>
</body>
</html>
```